Commercial Loan Originator Business Card (CHANGE COLORS SCHEME)

CHANGE COLOR SCHEME - SAME DESIGN

Name Marlene Agate
Title Commercial Loan Originator
Office (800) 417-2906 x68
Direct (240) 615-2043
Email freshgreens4life@quillbox.example

Name Dale Morrow
Office (800) 417-2906 x70
Direct (410) 392-5184
Email d.morthehomeguy@quillbox.example

Name Leonard Vasko
Office (800) 417-2906 x71
Direct (215) 463-0712
Email l.vasko41@quillbox.example

Name Gwen Halsey
Office (800) 417-2906 x
Direct (202) 548-1370
Email ghalsey63@quillbox.example

Name Mirna Ashby
Office (800) 417-2906 x72
Direct (240) 871-4526
Email tristatehomelending@quillbox.example

```html
<!DOCTYPE html>
<html lang="en">
<head>
<meta charset="utf-8">
<title>Gwen Halsey — Commercial Loan Originator</title>
<link href="https://fonts.googleapis.com/css2?family=Playfair+Display:wght@400&family=Poppins:wght@400;500&display=swap" rel="stylesheet">
<style>
  :root {
    --backdrop: #989898;
    --paper: #fbfbfb;
    --paper-shade: #efefef;
    --gold-light: #fcd77e;
    --gold-mid: #e0b35a;
    --gold-deep: #b98f45;
    --navy: #1d3f96;
    --navy-bright: #2f5fc4;
    --navy-deep: #0f2a78;
    --ink: #1b1b1b;
  }
  * { box-sizing: border-box; margin: 0; padding: 0; }
  html, body { width: 1200px; height: 1196px; overflow: hidden; }
  body { background: var(--backdrop); position: relative; font-family: "Poppins", sans-serif; }

  .card {
    position: absolute; left: 180px; width: 840px; height: 480px; overflow: hidden;
    background: linear-gradient(120deg, #ffffff 0%, var(--paper) 40%, var(--paper-shade) 65%, #ffffff 100%);
    box-shadow: 14px 14px 24px rgba(0,0,0,.35);
  }
  .card--front { top: 74px; }
  .card--back { top: 594px; }

  .gold-band {
    position: absolute; left: 0; top: 0; width: 112px; height: 100%;
    background: linear-gradient(100deg, var(--gold-deep) 0%, var(--gold-light) 40%, var(--gold-mid) 70%, var(--gold-deep) 100%);
  }

  .gold-text {
    font-family: "Playfair Display", serif; font-weight: 400; text-transform: uppercase;
    background-image: linear-gradient(180deg, var(--gold-deep) 0%, var(--gold-light) 55%, var(--gold-mid) 100%);
    -webkit-background-clip: text; background-clip: text; color: transparent;
  }
  .name { position: absolute; white-space: nowrap; font-weight: 400; }
  .name-line { display: block; width: max-content; }

  /* front */
  .photo-frame { position: absolute; left: 130px; top: 72px; width: 324px; height: 336px;
    border: 2px solid var(--navy); border-left: 0; }
  .photo-frame::before { content: ""; position: absolute; left: 0; top: -2px; width: 2px; height: 12px; background: var(--navy); }
  .photo-frame::after { content: ""; position: absolute; left: 0; bottom: -2px; width: 2px; height: 14px; background: var(--navy); }
  .portrait {
    position: absolute; left: 42px; top: 83px; width: 398px; height: 314px;
    border: 3px solid #ffffff;
    background: linear-gradient(110deg, #5f8a4a 0%, #6e6a5c 35%, #8a5a4c 60%, #c77a6a 85%, #b88274 100%);
  }
  .card--front .name { left: 482px; top: 129px; font-size: 73px; line-height: 70px; }
  .title-rule { position: absolute; left: 484px; top: 285px; width: 156px; height: 2px; background: var(--navy); }
  .job-title { position: absolute; left: 485px; top: 300px; font-size: 19px; line-height: 23px; color: var(--ink); }

  /* back */
  .name-frame { position: absolute; left: 187px; top: 66px; width: 505px; height: 112px; border: 2px solid var(--navy); }
  .card--back .name { left: 196px; top: 33px; font-size: 87px; line-height: 82px; }
  .card--back .name-line { background: #fbfbfb; padding: 0 10px 0 14px; }

  .contact-list { position: absolute; left: 186px; top: 239px; list-style: none; }
  .contact-list li { display: flex; align-items: center; height: 46px; margin-bottom: 7px; font-size: 30px; color: var(--ink); white-space: nowrap; }
  .contact-list li:nth-child(3) { margin-top: 4px; }
  .contact-list svg { width: 46px; height: 46px; margin-right: 14px; flex: none; }
</style>
</head>
<body>

<section class="card card--front">
  <div class="gold-band"></div>
  <div class="photo-frame"></div>
  <div class="portrait" role="img" aria-label="Portrait photo of Gwen Halsey"></div>
  <h1 class="name"><span class="name-line gold-text">Gwen</span><span class="name-line gold-text">Halsey</span></h1>
  <div class="title-rule"></div>
  <p class="job-title">Commercial Loan<br>Originator</p>
</section>

<section class="card card--back">
  <div class="gold-band"></div>
  <div class="name-frame"></div>
  <h2 class="name"><span class="name-line"><span class="gold-text">Gwen</span></span><span class="name-line"><span class="gold-text">Halsey</span></span></h2>

  <ul class="contact-list">
    <li>
      <svg viewBox="0 0 46 46" aria-hidden="true"><defs><linearGradient id="iconFill" x1="0" y1="0" x2="0" y2="1"><stop offset="0" stop-color="#2f5fc4"/><stop offset="1" stop-color="#0f2a78"/></linearGradient></defs>
        <circle cx="23" cy="23" r="23" fill="url(#iconFill)"/>
        <path d="M12 19c0-4 5-5 11-5s11 1 11 5v2h-5v-2h-12v2h-5z" fill="#fff"/>
        <rect x="15" y="22" width="16" height="11" rx="2" fill="#fff"/>
        <g fill="#1d3f96"><rect x="19" y="25" width="2" height="2"/><rect x="22" y="25" width="2" height="2"/><rect x="25" y="25" width="2" height="2"/><rect x="19" y="28" width="2" height="2"/><rect x="22" y="28" width="2" height="2"/><rect x="25" y="28" width="2" height="2"/></g>
      </svg>(800) 417-2906 x
    </li>
    <li>
      <svg viewBox="0 0 46 46" aria-hidden="true"><circle cx="23" cy="23" r="23" fill="url(#iconFill)"/>
        <path d="M15 13l4-1 3 6-3 2c1 3 3 5 6 6l2-3 6 3-1 4c-1 2-4 2-7 0-5-3-9-7-11-12-1-2 0-4 1-5z" fill="#fff"/>
        <path d="M25 13a9 9 0 0 1 8 8M25 17a5 5 0 0 1 4 4" stroke="#fff" stroke-width="2" fill="none" stroke-linecap="round"/>
      </svg>(202) 548-1370
    </li>
    <li>
      <svg viewBox="0 0 46 46" aria-hidden="true"><circle cx="23" cy="23" r="23" fill="url(#iconFill)"/>
        <rect x="11" y="15" width="24" height="16" fill="#fff"/>
        <path d="M11 15l12 10 12-10M11 31l9-8M35 31l-9-8" stroke="#1d3f96" stroke-width="1.6" fill="none"/>
      </svg>ghalsey63@quillbox.example
    </li>
  </ul>
</section>

</body>
</html>
```